established boer goat stud and dorper sheep stud need an updated look

I need a design to promote the boer goat stud and dorper sheep stud, so its clear and simple
Updates

Details for business card design Wirrabel Boers and Dorper Sheep Stud. I would like silhouette animal head or full body of a boer goat (not a dairy breed goat) and Dorper sheep. Contact: Maree Dalton +61 412578304 Sandra Pollock +61 438615027 Mooroopna North Victoria Australia Email: wirrabel5184@mailvane.com

Industry/Entity Type

Agriculture

Contact Information for Business Card

Wirrabel Boers and Dorper Sheep Stud Maree Dalton +61 412578304 Sandra Pollock +61 438615027 wirrabel5184@mailvane.com Wattlebrook Victoria Australia

Colors
EE7325
F08F49
F5BC92
FAE3D3
FDF4ED

Requirements
Must have
• My Boer Goats and Dorper Sheep images see my photos

```html
<!DOCTYPE html>
<html lang="en">
<head>
<meta charset="utf-8">
<title>Wirrabel Boers and Dorper Sheep Stud – Business Card</title>
<link href="https://fonts.googleapis.com/css2?family=Bebas+Neue&family=Arimo:wght@400;700&display=swap" rel="stylesheet">
<style>
  :root {
    --backdrop: #2f2f2f;
    --card-white: #ffffff;
    --ink: #111111;
    --band: #0c0c0c;
    --band-text: #ffffff;
    --pasture-green: #6f9a45;
    --fleece: #e9e4d8;
    --soil: #8d8478;
    --soil-light: #b5aca0;
  }
  * { box-sizing: border-box; margin: 0; padding: 0; }
  html, body { width: 1200px; height: 900px; overflow: hidden; }
  body {
    background: var(--backdrop);
    display: flex;
    flex-direction: column;
    align-items: center;
    justify-content: center;
    gap: 60px;
  }
  .card {
    position: relative;
    width: 600px;
    height: 345px;
    border-radius: 26px;
    overflow: hidden;
  }

  /* Front: contact side */
  .card-front { background: var(--card-white); }
  .contacts {
    position: absolute;
    left: 34px;
    top: 38px;
    font-family: "Arimo", Arial, sans-serif;
    font-size: 16px;
    line-height: 1.45;
    color: var(--ink);
    text-transform: uppercase;
  }
  .title-band {
    position: absolute;
    left: 0;
    top: 112px;
    width: 340px;
    height: 92px;
    background: var(--band);
    padding: 8px 0 0 34px;
    font-family: "Bebas Neue", Impact, sans-serif;
    color: var(--band-text);
    line-height: 0.95;
  }
  .title-band .title-main { font-size: 44px; letter-spacing: 1px; display: block; }
  .title-band .title-sub { font-size: 30px; letter-spacing: 1px; display: block; }
  .details {
    position: absolute;
    left: 34px;
    top: 226px;
    font-family: "Arimo", Arial, sans-serif;
    font-size: 16px;
    line-height: 1.55;
    color: var(--ink);
  }
  .details b { font-weight: 700; }
  .photo-circle {
    position: absolute;
    left: 318px;
    top: -40px;
    width: 430px;
    height: 430px;
    border-radius: 50%;
    border: 5px solid var(--band);
    background: radial-gradient(circle at 40% 45%, var(--fleece) 0%, var(--fleece) 38%, var(--pasture-green) 75%);
  }

  /* Back: photo side */
  .card-back {
    background: linear-gradient(160deg, var(--soil-light) 0%, var(--fleece) 45%, var(--soil) 100%);
  }
  .back-photo {
    position: absolute;
    inset: 0;
    background: linear-gradient(180deg, rgba(111,154,69,0.35) 0%, rgba(111,154,69,0) 30%);
  }
  .back-title {
    position: absolute;
    left: 0;
    right: 0;
    top: 112px;
    text-align: center;
    font-family: "Bebas Neue", Impact, sans-serif;
    font-size: 40px;
    letter-spacing: 2px;
    color: var(--ink);
  }
</style>
</head>
<body>
  <section class="card card-front">
    <div class="contacts">
      <p>Maree Dalton +61 412578304</p>
      <p>Sandra Pollock +61 438615027</p>
    </div>
    <h1 class="title-band">
      <span class="title-main">Wirrabel Boers</span>
      <span class="title-sub">&amp; Dorper Sheep Stud</span>
    </h1>
    <div class="details">
      <p><b>E</b> : wirrabel5184@mailvane.com</p>
      <p><b>A</b> : Wattlebrook Victoria Australia</p>
    </div>
    <div class="photo-circle" role="img" aria-label="Photo of two Dorper sheep with black heads and white bodies on green grass"></div>
  </section>

  <section class="card card-back">
    <div class="back-photo" role="img" aria-label="Photo of Boer goats with brown heads and white bodies standing on dirt ground"></div>
    <h2 class="back-title">Wirrabel Boers &amp; Dorper Sheep Stud</h2>
  </section>
</body>
</html>
```